One Pager Fact Sheet Design

I need a couple of headers and footer designed to use for information security fact sheets to give to customers. Similar to the one listed below.

```html
<!DOCTYPE html>
<html lang="en">
<head>
<meta charset="utf-8">
<title>Fact Sheet: TrickBot Malware</title>
<link href="https://fonts.googleapis.com/css2?family=Montserrat:wght@400;500;600;700;800&display=swap" rel="stylesheet">
<style>
:root{
  --red:#e30613;
  --charcoal:#58595b;
  --ink:#3a3a3a;
  --text:#4a4a4a;
  --panel:#ececec;
  --white:#ffffff;
  --page:#f2f2f2;
}
*{margin:0;padding:0;box-sizing:border-box}
html,body{width:783px;height:1200px;overflow:hidden;background:var(--page)}
body{font-family:'Montserrat',sans-serif;color:var(--text)}
.sheet{position:relative;width:783px;height:1200px;background:var(--white);overflow:hidden}
.abs{position:absolute}
.header-art{position:absolute;left:0;top:0}
.brand{position:absolute;left:36px;top:66px;display:flex;align-items:center;gap:10px}
.brand-dot{width:30px;height:30px;border-radius:50%;background:var(--red)}
.brand-name{font-weight:800;font-size:33px;color:var(--red);letter-spacing:-0.5px;line-height:1}
.title{position:absolute;left:36px;top:166px;color:var(--white)}
.title .lead{font-weight:700;font-size:37px;line-height:44px}
.title .main{font-weight:700;font-size:35px;line-height:44px;letter-spacing:0.5px}
.topics{position:absolute;left:30px;top:282px;display:flex;color:#e6e6e6;font-size:7.5px}
.topic{display:flex;flex-direction:column;align-items:center;gap:3px;padding:0 5px;border-right:1px solid #8a8a8a}
.topic:last-child{border-right:none}
.topic svg{width:13px;height:13px}
.section-title{position:absolute;left:36px;font-weight:700;font-size:22px;color:var(--ink);letter-spacing:0.3px;line-height:26px}
.section-title .accent{color:var(--red)}
.section-title::after{content:"";position:absolute;left:0;bottom:-9px;width:32px;height:2px;background:var(--charcoal)}
.summary-text{position:absolute;left:36px;top:412px;width:728px;font-size:11.8px;line-height:15.5px}
.panel{position:absolute;left:0;top:565px;width:783px;height:565px;background:var(--panel)}
.block{position:absolute}
.block-icon{position:absolute;left:0;top:0;width:40px;height:40px}
.block-body{margin-left:54px}
.block h3{font-size:17.5px;font-weight:700;color:var(--red);line-height:20px;margin-top:5px;margin-bottom:7px}
.block p{font-size:11.4px;line-height:15px;margin-bottom:13px}
.block ul{list-style:none;margin:0 0 14px 0}
.block li{position:relative;padding-left:20px;font-size:11.2px;line-height:15px;font-weight:700;color:var(--ink);margin-bottom:11px}
.block li.tight{margin-bottom:3px}
.block li::before{content:"";position:absolute;left:2px;top:3px;width:9px;height:9px;border-radius:50%;background:var(--red)}
.block li::after{content:"";position:absolute;left:4.5px;top:5px;width:3px;height:3px;border-right:1.4px solid #fff;border-bottom:1.4px solid #fff;transform:rotate(40deg)}
.block .sub{padding-left:40px;position:relative;font-size:11.2px;line-height:14.5px;margin-top:-2px}
.block .sub::before{content:"";position:absolute;left:23px;top:4px;width:7px;height:7px;border-radius:50%;background:var(--red)}
.indent{padding-left:2px}
.footer-contact{position:absolute;left:40px;top:1140px;color:var(--white);display:flex;gap:30px;font-weight:700;font-size:17px;align-items:center}
.footer-contact span{display:flex;align-items:center;gap:7px}
.footer-contact svg{width:16px;height:16px}
.footer-contact .mail{font-size:14.5px}
.footer-lines{position:absolute;left:40px;top:1171px;color:var(--white);font-size:8.2px;font-weight:700}
.footer-web{position:absolute;left:560px;top:1155px;font-weight:700;font-size:13.5px;letter-spacing:1.5px;color:var(--ink);display:flex;align-items:center;gap:10px}
.footer-web svg{width:13px;height:13px}
</style>
</head>
<body>
<main class="sheet">

  <svg class="header-art" width="783" height="400" viewBox="0 0 783 400">
    <defs>
      <radialGradient id="cityGlow" cx="50%" cy="45%" r="60%">
        <stop offset="0" stop-color="#5a8fbf"/>
        <stop offset="0.55" stop-color="#234a72"/>
        <stop offset="1" stop-color="#0d1f36"/>
      </radialGradient>
    </defs>
    <path d="M0 145 H468 Q486 240 494 337 H0 Z" fill="#58595b"/>
    <circle cx="635" cy="233" r="150" fill="#e30613"/>
    <circle cx="642" cy="228" r="135" fill="#ffffff"/>
    <circle cx="644" cy="226" r="130" fill="url(#cityGlow)" role="img" aria-label="Night city skyline photograph with glowing network connection lines"/>
  </svg>

  <div class="brand">
    <div class="brand-dot"></div>
    <div class="brand-name">northgrid systems</div>
  </div>

  <div class="title">
    <div class="lead">Fact Sheet:</div>
    <div class="main">TRICKBOT MALWARE</div>
  </div>

  <div class="topics">
    <div class="topic"><svg viewBox="0 0 14 14"><circle cx="7" cy="7" r="5.5" fill="none" stroke="#fff" stroke-width="1.5"/><rect x="6.2" y="4" width="1.6" height="6" fill="#fff"/></svg>It Security</div>
    <div class="topic"><svg viewBox="0 0 14 14"><rect x="1" y="2" width="4" height="4" fill="#fff"/><rect x="9" y="2" width="4" height="4" fill="#fff"/><rect x="5" y="8" width="4" height="4" fill="#fff"/></svg>Supply Chain</div>
    <div class="topic"><svg viewBox="0 0 14 14"><path d="M7 1 L12 3 V7 Q12 11 7 13 Q2 11 2 7 V3 Z" fill="#fff"/></svg>Ot Security</div>
    <div class="topic"><svg viewBox="0 0 14 14"><rect x="2" y="3" width="10" height="7" fill="none" stroke="#fff" stroke-width="1.4"/><rect x="5" y="11" width="4" height="1.5" fill="#fff"/></svg>Insider Threat</div>
    <div class="topic"><svg viewBox="0 0 14 14"><path d="M7 1 L12 3 V7 Q12 11 7 13 Q2 11 2 7 V3 Z" fill="none" stroke="#fff" stroke-width="1.4"/></svg>Physical Security</div>
    <div class="topic"><svg viewBox="0 0 14 14"><circle cx="7" cy="7" r="5.5" fill="none" stroke="#fff" stroke-width="1.2"/><path d="M1.5 7 H12.5 M7 1.5 V12.5" stroke="#fff" stroke-width="1"/></svg>Interoperable Communications</div>
  </div>

  <h2 class="section-title" style="top:358px"><span class="accent">SUMMARY</span></h2>
  <p class="summary-text">TrickBot malware—first identified in 2016—is a Trojan developed and operated by a sophisticated group of cybercrime actors. The cybercrime group initially designed TrickBot as a banking trojan to steal financial data. Through continued development and new functionality, TrickBot has become a highly modular, multi-stage malware that provides its operators a full suite of tools to conduct a myriad of illegal cyber activities. Since TrickBot's inception, the cybercrime group has used the malware to attack individuals and businesses globally across a wide range of sectors.</p>

  <h2 class="section-title" style="top:513px"><span class="accent">KEY</span> TAKEAWAYS</h2>

  <section class="panel"></section>

  <svg width="0" height="0" style="position:absolute">
    <symbol id="badge" viewBox="0 0 40 40">
      <circle cx="20" cy="20" r="18" fill="#fff" stroke="#e30613" stroke-width="2.5"/>
      <circle cx="20" cy="20" r="12" fill="#e30613"/>
    </symbol>
  </svg>

  <div class="block" style="left:34px;top:603px;width:324px">
    <svg class="block-icon"><use href="#badge"/><circle cx="20" cy="17" r="4" fill="#fff"/><path d="M13 26 Q20 19 27 26 Z" fill="#fff"/></svg>
    <div class="block-body">
      <h3>TrickBot Operators</h3>
      <p>Are a sophisticated cybercrime group known by several aliases in open-source reporting, including</p>
      <ul>
        <li class="tight">Wizard Spider (Skyward Labs),1</li>
        <li class="tight">UNC1878 (Redline Intel), and</li>
        <li>Gold Blackburn (Harbor Watch).2</li>
      </ul>
      <p class="indent">Employ malware from other 'trusted' cybercrime actors, including Emotet3 and Bokbot.4, 5</p>
      <p class="indent">Enable high impact "big game hunting" ransomware attacks.</p>
      <p class="indent">Have a toolset capable of using the entire cyber kill chain, from delivery to post-exploitation.6</p>
    </div>
  </div>

  <div class="block" style="left:34px;top:950px;width:324px">
    <svg class="block-icon"><use href="#badge"/><rect x="14" y="15" width="12" height="9" fill="#fff"/></svg>
    <div class="block-body">
      <h3>Initial Access</h3>
      <p>The TrickBot operators typically achieve initial access through the following infection vectors:</p>
      <ul>
        <li>Spearphishing campaigns use tailored emails that contain malicious links or documents that contain macros, which if enabled—execute malware.</li>
      </ul>
    </div>
  </div>

  <div class="block" style="left:404px;top:603px;width:346px">
    <svg class="block-icon"><use href="#badge"/><path d="M15 25 L25 15 M20 15 H25 V20" stroke="#fff" stroke-width="2.2" fill="none"/></svg>
    <div class="block-body">
      <h3>Execution</h3>
      <p>The TrickBot operators may</p>
      <ul>
        <li>Execute TrickBot as either a first- or second-stage payload;</li>
        <li>Deploy additional malware (e.g., Ryuk7 and Conti ransomware, Emotet downloader); and</li>
        <li>Load TrickBot into networks using other malware to achieve additional objectives.</li>
      </ul>
    </div>
  </div>

  <div class="block" style="left:404px;top:822px;width:346px">
    <svg class="block-icon"><use href="#badge"/><circle cx="20" cy="20" r="5" fill="none" stroke="#fff" stroke-width="2.2"/><circle cx="20" cy="20" r="1.6" fill="#fff"/></svg>
    <div class="block-body">
      <h3>Capabilities</h3>
      <p>TrickBot may be usedspearphishing, spam campaigns, malvertising, and network vulnerabilities (e.g., Server Message Block).</p>
      <ul>
        <li>To exfiltrate data (e.g., email, credentials, point-of-sale info);</li>
        <li>For cryptomining; and</li>
        <li>For host enumeration (e.g., reconnaissance of Unified Extensible Firmware Interface or Basic Input/Output System [UEFI/BIOS] firmware).8</li>
      </ul>
      <p class="sub">For host enumeration, the operators deliver TrickBot in modules containing a configuration file with specific tasks.</p>
    </div>
  </div>

  <svg class="abs" style="left:0;top:1118px" width="783" height="82" viewBox="0 0 783 82">
    <path d="M0 0 H783 V82 H0 Z" fill="#ffffff"/>
    <path d="M0 6 H410 Q505 4 545 82 H0 Z" fill="#e30613"/>
    <path d="M548 68 H783 V82 H554 Z" fill="#58595b"/>
  </svg>

  <div class="footer-contact">
    <span><svg viewBox="0 0 16 16"><path d="M3 1.5 L6 1.5 L7 5 L5 6.5 Q6.5 9.5 9.5 11 L11 9 L14.5 10 V13 Q14.5 14.5 13 14.5 Q3 13.5 1.5 3 Q1.5 1.5 3 1.5 Z" fill="#fff"/></svg>1-800-555-0147</span>
    <span class="mail"><svg viewBox="0 0 16 16"><rect x="1" y="3" width="14" height="10" fill="none" stroke="#fff" stroke-width="1.5"/><path d="M1 3 L8 9 L15 3" fill="none" stroke="#fff" stroke-width="1.5"/></svg>hello@northgridsys.com</span>
  </div>
  <div class="footer-lines">desk@alertnet.example (UNCLASS) | ops@alertnet-s.example (SIPRNET) | ops@alertnet-j.example (JWICS)</div>

  <div class="footer-web">
    <svg viewBox="0 0 14 14"><circle cx="7" cy="7" r="6" fill="none" stroke="#e30613" stroke-width="1.3"/><ellipse cx="7" cy="7" rx="2.6" ry="6" fill="none" stroke="#e30613" stroke-width="1"/><path d="M1 7 H13" stroke="#e30613" stroke-width="1"/></svg>
    www.northgridsys.com
  </div>

</main>
</body>
</html>
```